Automotive component supplier needs a business card design

We need a business card design for our company called Velran Global Components Ltd based in the UK. We are a supplier of interior and exterior components to premium car manufacturers such as Corvel Ashby, Hadley Fenn, Marquist and Tavarelli. We would like to see a modern business card design that uses the colour blue.

Target Market(s)

Premium automotive car manufacturers.

Industry/Entity Type

Automotive

Contact Information for Business Card

Company Name : Velran Global Components Limited
Address: 17 Marlow Yard, Upper Heath, Warwick, CV31 8QL, United Kingdom
Web Address : www.velrancomponents-example.co.uk

Font styles to use
Other font styles liked:
• Helvetica

Colors
3176b5
0255a3
85acd3
cfdeed
cee9f5
85cae6
34a6d7
0692cd
9bcb3c

Requirements
Must have
• Clear company logo and a mixture of blue colours.
Nice to have
• A high quality modern image.
Should not have
• Multiple colours.

```html
<!DOCTYPE html>
<html lang="en">
<head>
<meta charset="utf-8">
<title>Velran Global Components – Business Card</title>
<link href="https://fonts.googleapis.com/css2?family=Roboto:wght@400;700&display=swap" rel="stylesheet">
<style>
  :root {
    --backdrop: #262626;
    --card-white: #ffffff;
    --brand-blue: #0692cd;
    --accent-green: #9bcb3c;
    --text-grey: #4a4a4a;
  }
  html, body {
    margin: 0;
    padding: 0;
    width: 1200px;
    height: 987px;
    overflow: hidden;
    background: var(--backdrop);
    font-family: "Roboto", Helvetica, Arial, sans-serif;
  }
  .card {
    position: absolute;
    width: 615px;
    height: 352px;
  }
  .card-front { left: 293px; top: 130px; background: var(--card-white); }
  .card-back { left: 292px; top: 505px; background: var(--brand-blue); }

  .wordmark {
    position: absolute;
    color: var(--brand-blue);
    line-height: 1;
    margin: 0;
    white-space: nowrap;
  }
  .wordmark-name { font-weight: 700; }
  .wordmark-sub { font-weight: 400; }
  .card-front .wordmark-name { left: 33px; top: 38px; font-size: 65px; letter-spacing: 2px; }
  .card-front .wordmark-sub { left: 35px; top: 106px; font-size: 14.5px; letter-spacing: 4.6px; }

  .address {
    position: absolute;
    left: 35px; top: 155px;
    font-size: 15.5px;
    line-height: 22px;
    color: var(--text-grey);
    font-style: normal;
  }
  .contact-list {
    position: absolute;
    left: 35px; top: 232px;
    list-style: none;
    margin: 0; padding: 0;
    font-size: 15.5px;
    color: var(--text-grey);
  }
  .contact-list li {
    display: flex;
    align-items: center;
    height: 23.5px;
  }
  .contact-list svg { width: 15px; height: 15px; margin-right: 8px; fill: var(--brand-blue); }
  .contact-list li.small { font-size: 14.5px; }

  .name-tag-square {
    position: absolute;
    left: 348px; top: 211px;
    width: 62px; height: 61px;
    background: var(--accent-green);
    border-radius: 6px;
    box-shadow: 2px 0 0 #fff;
    z-index: 2;
  }
  .name-tag-band {
    position: absolute;
    left: 405px; top: 211px;
    width: 210px; height: 61px;
    background: var(--brand-blue);
    color: #fff;
    text-align: right;
    box-sizing: border-box;
    padding: 6px 28px 0 0;
  }
  .person-name { font-size: 20px; font-weight: 700; margin: 0; letter-spacing: 0.3px; }
  .person-role { font-size: 15px; margin: 3px 0 0; }

  .card-back .wordmark { color: #fff; width: 100%; text-align: center; left: 0; }
  .card-back .wordmark-name { top: 118px; font-size: 88px; letter-spacing: 4px; }
  .card-back .wordmark-sub { top: 204px; font-size: 20px; letter-spacing: 6px; }
  .back-url {
    position: absolute;
    left: 0; width: 100%;
    top: 292px;
    text-align: center;
    color: #fff;
    font-size: 15px;
    letter-spacing: 3px;
    margin: 0;
  }
</style>
</head>
<body>
  <section class="card card-front">
    <h1 class="wordmark wordmark-name">VELRAN</h1>
    <p class="wordmark wordmark-sub">GLOBAL COMPONENTS</p>

    <address class="address">
      17 Marlow Yard, Upper Heath<br>
      Warwick, CV31 8QL<br>
      United Kingdom
    </address>

    <ul class="contact-list">
      <li><svg viewBox="0 0 24 24"><path d="M6.6 10.8a15.1 15.1 0 0 0 6.6 6.6l2.2-2.2a1 1 0 0 1 1-.25 11.4 11.4 0 0 0 3.6.57 1 1 0 0 1 1 1V20a1 1 0 0 1-1 1A17 17 0 0 1 3 4a1 1 0 0 1 1-1h3.5a1 1 0 0 1 1 1c0 1.25.2 2.45.57 3.57a1 1 0 0 1-.25 1z"/></svg>744 219 6083</li>
      <li><svg viewBox="0 0 24 24"><path d="M7 1h10a2 2 0 0 1 2 2v18a2 2 0 0 1-2 2H7a2 2 0 0 1-2-2V3a2 2 0 0 1 2-2zm0 3v14h10V4zm5 15.5a1.2 1.2 0 1 0 0 2.4 1.2 1.2 0 0 0 0-2.4z"/></svg>755 302 1847</li>
      <li class="small"><svg viewBox="0 0 24 24"><path d="M2 5h20v14H2zm2 2v.5l8 5 8-5V7zm0 2.8V17h16V9.8l-8 5z"/></svg>daniel@velrancomponents-example.co.uk</li>
      <li class="small"><svg viewBox="0 0 24 24"><path d="M12 2a10 10 0 1 0 0 20 10 10 0 0 0 0-20zm-1 17.9A8 8 0 0 1 4.2 10L9 14.8v1a2 2 0 0 0 2 2zm6.9-2.5A2 2 0 0 0 16 16h-1v-3a1 1 0 0 0-1-1H8v-2h2a1 1 0 0 0 1-1V7h2a2 2 0 0 0 2-2v-.4a8 8 0 0 1 2.9 12.8z"/></svg>www.velrancomponents-example.co.uk</li>
    </ul>

    <span class="name-tag-square"></span>
    <div class="name-tag-band">
      <p class="person-name">DANIEL HARROW</p>
      <p class="person-role">CEO/Founder</p>
    </div>
  </section>

  <section class="card card-back">
    <p class="wordmark wordmark-name">VELRAN</p>
    <p class="wordmark wordmark-sub">GLOBAL COMPONENTS</p>
    <p class="back-url">www.velrancomponents-example.co.uk</p>
  </section>
</body>
</html>
```